Executive recruiting firm in need of business card design

Executive recruiting firm looking for a sleek, classy and modern business card design; card itself will be square shape, rounded edges and soft touch paper, our colors are dark blues in the navy color scale, silvers and grays. Reference our website for a better idea of our company's feel and goals at Tarvex-Up.com - our company message is "Employee Engagement Begins at Recruitment" this should be on the card

```html
<!DOCTYPE html>
<html lang="en">
<head>
<meta charset="utf-8">
<title>Tarvex Up – Business Card</title>
<link rel="stylesheet" href="https://fonts.googleapis.com/css2?family=Arimo:wght@400;700&display=swap">
<style>
  :root {
    --navy: #1e1f44;
    --ink: #1a1b3a;
    --paper: #ffffff;
    --canvas: #ffffff;
    --edge: #e2e2e6;
  }
  * { margin: 0; padding: 0; box-sizing: border-box; }
  html, body {
    width: 1200px;
    height: 1000px;
    overflow: hidden;
    background: var(--canvas);
    font-family: "Arimo", Arial, sans-serif;
  }
  .stage {
    position: relative;
    width: 1200px;
    height: 1000px;
  }
  .card {
    position: absolute;
    top: 290px;
    width: 420px;
    height: 420px;
    border-radius: 28px;
  }
  .card-front {
    left: 170px;
    background: var(--navy);
  }
  .card-back {
    left: 620px;
    background: var(--paper);
    border: 1px solid var(--edge);
    color: var(--ink);
  }
  .brand {
    position: absolute;
    right: 48px;
    bottom: 84px;
    text-align: right;
    color: var(--paper);
  }
  .brand-name {
    font-size: 30px;
    font-weight: 400;
    letter-spacing: 4px;
    line-height: 1;
  }
  .brand-message {
    margin-top: 8px;
    font-size: 9px;
    font-weight: 400;
    letter-spacing: 1px;
  }
  .holder {
    position: absolute;
    left: 58px;
    top: 80px;
    font-size: 22px;
    line-height: 1.15;
    letter-spacing: -0.3px;
  }
  .holder-name strong { font-weight: 700; }
  .contact {
    position: absolute;
    left: 130px;
    top: 318px;
    list-style: none;
    font-size: 15px;
  }
  .contact li {
    display: flex;
    align-items: center;
    gap: 10px;
    height: 26px;
  }
  .contact svg {
    width: 18px;
    height: 18px;
    fill: none;
    stroke: var(--ink);
    stroke-width: 1.5;
    stroke-linejoin: round;
    stroke-linecap: round;
  }
</style>
</head>
<body>
<main class="stage">
  <section class="card card-front" aria-label="Card front">
    <div class="brand">
      <p class="brand-name">TARVEX UP</p>
      <p class="brand-message">Employee Engagement Begins at Recruitment</p>
    </div>
  </section>

  <section class="card card-back" aria-label="Card back">
    <div class="holder">
      <p class="holder-name">Loresum <strong>ipsum</strong></p>
      <p class="holder-role">Président</p>
    </div>
    <ul class="contact">
      <li>
        <svg viewBox="0 0 20 20" aria-hidden="true"><circle cx="10" cy="10" r="8.5"/><path d="M7 5.5l1.6 2.2-1 1.2c.7 1.4 1.7 2.4 3 3l1.2-1 2.2 1.6-.9 1.6c-3.4-.3-6.5-3.4-6.8-6.8z"/></svg>
        <span>(418)-555-0142</span>
      </li>
      <li>
        <svg viewBox="0 0 20 20" aria-hidden="true"><path d="M2 10L10 3l8 7M4.5 8v9h4v-5h3v5h4V8"/></svg>
        <span>www.tarvex-Up.com</span>
      </li>
      <li>
        <svg viewBox="0 0 20 20" aria-hidden="true"><rect x="2" y="4.5" width="16" height="11"/><path d="M2 4.5l8 6.5 8-6.5M2 15.5l6-5M18 15.5l-6-5"/></svg>
        <span>tarvex.up@Tarvex-Up.com</span>
      </li>
    </ul>
  </section>
</main>
</body>
</html>
```